Business Card Design For Marketing Agnecy LVP

Need business card design for marketing agency.

Doug Fenwick
President, CEO
1-555-302-4196
doug@boldpromoperksgroup.example
www.BoldPromoPerksGroup.example

Back Side:
Boost Sales Using Rewards, Incentives & Giveaways
Get A Free Sample Package

Target Market(s)

B2B

Industry/Entity Type

Marketing

Contact Information for Business Card

Doug Fenwick
President, CEO
1-555-302-4196

Back Side:
Get A Free Sample Package

Please note that my current url is OLD DESIGN. I am working on new design and want the business card to match color themes at least on new site. Here is the demo link for new site so you can see the colors I use, etc.

http://layoutcratehub.example/kq/doug/lvp_final/index.html

Requirements
Must have
• Please note that my current url is OLD DESIGN. I am working on new design and want the business card to match color themes at least on new site. Here is the demo link for new site so you can see the colors I use, etc.

Nice to have

Should not have

```html
<!DOCTYPE html>
<html lang="en">
<head>
<meta charset="utf-8">
<title>LVP Business Card</title>
<link rel="stylesheet" href="https://fonts.googleapis.com/css2?family=Montserrat:wght@600;800&family=Roboto:wght@400;500;700&display=swap">
<style>
  :root {
    --bg: #c9c9c9;
    --brand-blue: #2b5797;
    --brand-blue-dark: #234a82;
    --card-white: #f2f2f2;
    --ink: #333333;
    --ink-soft: #444444;
    --action-green: #4caf35;
    --white: #ffffff;
  }
  * { margin: 0; padding: 0; box-sizing: border-box; }
  html, body { width: 1200px; height: 576px; overflow: hidden; background: var(--bg); }
  body { position: relative; font-family: "Roboto", Arial, sans-serif; }

  .card {
    position: absolute;
    width: 484px;
    height: 291px;
    border-radius: 10px;
  }
  .card--back { left: 82px; top: 139px; background: linear-gradient(180deg, var(--brand-blue) 0%, var(--brand-blue-dark) 100%); }
  .card--front { left: 602px; top: 138px; width: 480px; background: var(--card-white); }

  /* Back side */
  .brand-stack {
    position: absolute; left: 0; right: 0; top: 42px;
    display: flex; flex-direction: column; align-items: center; gap: 10px;
  }
  .brand-dot { width: 26px; height: 26px; border-radius: 50%; background: var(--white); }
  .brand-name--stacked {
    font-family: "Montserrat", Arial, sans-serif; font-weight: 800;
    color: var(--white); text-align: center; font-size: 34px; line-height: 1.05; letter-spacing: 1px;
  }
  .offer-banner { position: absolute; left: 62px; top: 194px; width: 358px; height: 52px; }
  .offer-banner svg { position: absolute; inset: 0; }
  .offer-banner__line {
    position: absolute; left: 0; right: 0; text-align: center; font-size: 13px; color: var(--ink);
  }
  .offer-banner__line--lead { top: 8px; }
  .offer-banner__line--cta { top: 26px; font-weight: 700; color: var(--brand-blue); }
  .back-url {
    position: absolute; left: 0; right: 0; top: 255px; text-align: center;
    color: var(--white); font-size: 13px;
  }

  /* Front side */
  .brand-row {
    position: absolute; left: 0; right: 0; top: 62px;
    display: flex; align-items: center; justify-content: center; gap: 12px;
  }
  .brand-row .brand-dot { background: var(--brand-blue); width: 34px; height: 34px; }
  .brand-name--inline {
    font-family: "Montserrat", Arial, sans-serif; font-weight: 800;
    color: var(--brand-blue); font-size: 25px; letter-spacing: 0.5px;
  }
  .person { position: absolute; right: 290px; top: 160px; text-align: right; }
  .person__name { font-size: 20px; font-weight: 700; color: var(--brand-blue); }
  .person__title { font-size: 12.5px; color: var(--ink-soft); margin-top: 3px; }
  .contacts { position: absolute; left: 220px; top: 156px; list-style: none; }
  .contacts li {
    display: flex; align-items: center; gap: 9px; height: 18.5px;
    font-size: 12.5px; color: var(--ink);
  }
  .contacts svg { width: 12px; height: 12px; fill: var(--brand-blue); flex: none; }
  .cta-button { position: absolute; left: 92px; top: 244px; width: 298px; height: 20px; }
  .cta-button svg { position: absolute; inset: 0; }
  .cta-button span {
    position: absolute; inset: 0; display: flex; align-items: center; justify-content: center;
    font-family: "Montserrat", Arial, sans-serif; font-weight: 800; font-size: 12.5px;
    color: var(--white); letter-spacing: 0.6px;
  }
</style>
</head>
<body>

<section class="card card--back" aria-label="Card back">
  <div class="brand-stack">
    <div class="brand-dot"></div>
    <div class="brand-name brand-name--stacked">BOLD PROMO<br>PERKS GROUP</div>
  </div>
  <div class="offer-banner">
    <svg viewBox="0 0 358 52" preserveAspectRatio="none" aria-hidden="true">
      <polygon points="0,0 358,0 350,42 179,52 8,42" fill="#f4f4f4"/>
    </svg>
    <p class="offer-banner__line offer-banner__line--lead">Boost Sales Using Rewards, Incentives &amp; Giveaways</p>
    <p class="offer-banner__line offer-banner__line--cta">GET A FREE SAMPLE PACKAGE</p>
  </div>
  <p class="back-url">www.BoldPromoPerksGroup.example</p>
</section>

<section class="card card--front" aria-label="Card front">
  <div class="brand-row">
    <div class="brand-dot"></div>
    <div class="brand-name brand-name--inline">BOLD PROMO PERKS GROUP</div>
  </div>
  <div class="person">
    <p class="person__name">Doug Fenwick</p>
    <p class="person__title">President, CEO</p>
  </div>
  <ul class="contacts">
    <li>
      <svg viewBox="0 0 24 24" aria-hidden="true"><path d="M6.6 10.8a15 15 0 0 0 6.6 6.6l2.2-2.2c.3-.3.7-.4 1-.2 1.1.4 2.3.6 3.6.6.6 0 1 .4 1 1V20c0 .6-.4 1-1 1A17 17 0 0 1 3 4c0-.6.4-1 1-1h3.5c.6 0 1 .4 1 1 0 1.3.2 2.5.6 3.6.1.3 0 .7-.2 1z"/></svg>
      1-555-302-4196
    </li>
    <li>
      <svg viewBox="0 0 24 24" aria-hidden="true"><path d="M2 5h20v14H2z M2 5l10 8 10-8" fill="none" stroke="#2b5797" stroke-width="2.4"/></svg>
      doug@boldpromoperksgroup.example
    </li>
    <li>
      <svg viewBox="0 0 24 24" aria-hidden="true"><circle cx="12" cy="12" r="9.5" fill="none" stroke="#2b5797" stroke-width="2"/><path d="M2.5 12h19M12 2.5c3 3 3 16 0 19M12 2.5c-3 3-3 16 0 19" fill="none" stroke="#2b5797" stroke-width="1.6"/></svg>
      www.BoldPromoPerksGroup.example
    </li>
  </ul>
  <div class="cta-button">
    <svg viewBox="0 0 298 20" preserveAspectRatio="none" aria-hidden="true">
      <polygon points="4,0 298,0 294,20 0,20" fill="#4caf35"/>
    </svg>
    <span>GET A FREE SAMPLE PACKAGE</span>
  </div>
</section>

</body>
</html>
```